KORV PTY LTD - Business Cards

Design a modern business card - using the attached Designs.
Same design as on the front, apart from the names/numbers/emails to be different.
We want the cards to be very glossy to stand out, do I think the simple black/white/metallic will be effective.
Both lots of details below:

Tom Wrenshaw
Director
tom_korv@nulvane.com
0438 274 093

Lewis Corbyn
Director
lewis_korv@nulvane.com
0419 385 642

Industry/Entity Type

Business

```html
<!DOCTYPE html>
<html lang="en">
<head>
<meta charset="utf-8">
<title>KORV PTY LTD – Business Cards</title>
<link href="https://fonts.googleapis.com/css2?family=Oswald:wght@400;600&family=Open+Sans:wght@400;600&display=swap" rel="stylesheet">
<style>
  :root {
    --stage: #e6e4e1;
    --card-white: #ffffff;
    --band-light: #e9e9e9;
    --band-mid: #d2d2d2;
    --panel-dark: #303436;
    --ink-dark: #2b2e30;
    --ink-light: #f4f4f4;
    --ink-muted: #c9cccd;
  }
  * { box-sizing: border-box; margin: 0; padding: 0; }
  html, body { width: 1200px; height: 970px; overflow: hidden; }
  body {
    background: var(--stage);
    font-family: "Open Sans", Arial, sans-serif;
    position: relative;
  }
  .card {
    position: absolute;
    left: 220px;
    width: 760px;
    height: 434px;
    overflow: hidden;
    background: var(--card-white);
    box-shadow: 0 6px 18px rgba(0,0,0,0.18);
  }
  .card--back { top: 34px; }
  .card--front { top: 502px; background: var(--panel-dark); }

  .back-band {
    position: absolute;
    left: 0; right: 0;
    top: 88px; height: 236px;
    background: linear-gradient(180deg, var(--band-light) 0%, var(--band-mid) 55%, var(--band-light) 100%);
  }
  .brand {
    position: absolute;
    display: flex;
    align-items: center;
    gap: 12px;
    transform: translate(-50%, -50%);
    white-space: nowrap;
  }
  .brand__dot {
    width: 22px; height: 22px;
    border-radius: 50%;
    background: var(--ink-dark);
  }
  .brand__name {
    font-family: "Oswald", Arial, sans-serif;
    font-weight: 600;
    font-size: 34px;
    letter-spacing: 2px;
    color: var(--ink-dark);
  }
  .card--back .brand { left: 50%; top: 206px; }

  .front-logo-area {
    position: absolute;
    left: 0; top: 110px;
    width: 372px; height: 324px;
    background: linear-gradient(135deg, #ffffff 0%, #ececec 100%);
  }
  .front-logo-area .brand { left: 50%; top: 50%; }
  .front-logo-area .brand__name { font-size: 28px; }
  .front-notch {
    position: absolute;
    left: 372px; top: 138px;
    width: 0; height: 0;
    border-top: 12px solid transparent;
    border-bottom: 12px solid transparent;
    border-left: 14px solid #fbfbfb;
  }

  .contact {
    position: absolute;
    left: 404px; top: 128px;
    color: var(--ink-light);
  }
  .contact__heading {
    display: flex;
    align-items: baseline;
    gap: 12px;
    margin-bottom: 34px;
  }
  .contact__name {
    font-family: "Oswald", Arial, sans-serif;
    font-weight: 600;
    font-size: 30px;
    letter-spacing: 1px;
    text-transform: uppercase;
  }
  .contact__role {
    font-family: "Oswald", Arial, sans-serif;
    font-weight: 400;
    font-size: 16px;
    letter-spacing: 2px;
    color: var(--ink-muted);
    text-transform: uppercase;
  }
  .contact__list { list-style: none; }
  .contact__item {
    display: flex;
    align-items: center;
    gap: 12px;
    font-size: 15px;
    margin-bottom: 14px;
  }
  .contact__icon {
    width: 22px; height: 22px;
    flex: none;
  }
</style>
</head>
<body>

<section class="card card--back" aria-label="Card back">
  <div class="back-band"></div>
  <div class="brand">
    <span class="brand__dot"></span>
    <span class="brand__name">KORV PTY LTD</span>
  </div>
</section>

<section class="card card--front" aria-label="Card front">
  <div class="front-logo-area">
    <div class="brand">
      <span class="brand__dot"></span>
      <span class="brand__name">KORV PTY LTD</span>
    </div>
  </div>
  <div class="front-notch"></div>

  <div class="contact">
    <div class="contact__heading">
      <span class="contact__name">Alex Marlow</span>
      <span class="contact__role">General Manager</span>
    </div>
    <ul class="contact__list">
      <li class="contact__item">
        <svg class="contact__icon" viewBox="0 0 22 22" aria-hidden="true">
          <circle cx="11" cy="11" r="10" fill="none" stroke="#f4f4f4" stroke-width="1.4"/>
          <path d="M8 6.5c-.8.6-1.2 1.5-.8 2.6.9 2.4 2.5 4.1 4.9 5.1 1.1.4 2 0 2.6-.8l-1.6-1.5-1.2.6c-1-.5-1.8-1.3-2.3-2.3l.6-1.2z" fill="#f4f4f4"/>
        </svg>
        <span>013 482 7150</span>
      </li>
      <li class="contact__item">
        <svg class="contact__icon" viewBox="0 0 22 22" aria-hidden="true">
          <circle cx="11" cy="11" r="10" fill="none" stroke="#f4f4f4" stroke-width="1.4"/>
          <path d="M8 6.5c-.8.6-1.2 1.5-.8 2.6.9 2.4 2.5 4.1 4.9 5.1 1.1.4 2 0 2.6-.8l-1.6-1.5-1.2.6c-1-.5-1.8-1.3-2.3-2.3l.6-1.2z" fill="#f4f4f4"/>
        </svg>
        <span>013 482 7150</span>
      </li>
      <li class="contact__item">
        <svg class="contact__icon" viewBox="0 0 22 22" aria-hidden="true">
          <circle cx="11" cy="11" r="10" fill="none" stroke="#f4f4f4" stroke-width="1.4"/>
          <rect x="6" y="7.5" width="10" height="7" fill="none" stroke="#f4f4f4" stroke-width="1.2"/>
          <path d="M6 7.5l5 4 5-4" fill="none" stroke="#f4f4f4" stroke-width="1.2"/>
        </svg>
        <span>alex@korvmail.com</span>
      </li>
      <li class="contact__item">
        <svg class="contact__icon" viewBox="0 0 22 22" aria-hidden="true">
          <circle cx="11" cy="11" r="10" fill="none" stroke="#f4f4f4" stroke-width="1.4"/>
          <circle cx="11" cy="11" r="5" fill="none" stroke="#f4f4f4" stroke-width="1.2"/>
          <path d="M6 11h10M11 6c-2 3-2 7 0 10M11 6c2 3 2 7 0 10" fill="none" stroke="#f4f4f4" stroke-width="1"/>
        </svg>
        <span>www.korvsite.com</span>
      </li>
      <li class="contact__item">
        <svg class="contact__icon" viewBox="0 0 22 22" aria-hidden="true">
          <circle cx="11" cy="11" r="10" fill="none" stroke="#f4f4f4" stroke-width="1.4"/>
          <path d="M11 5.5a3.6 3.6 0 0 0-3.6 3.6c0 2.7 3.6 7 3.6 7s3.6-4.3 3.6-7A3.6 3.6 0 0 0 11 5.5z" fill="#f4f4f4"/>
          <circle cx="11" cy="9.1" r="1.3" fill="#303436"/>
        </svg>
        <span>42 Hollin Road, 2nd building Street</span>
      </li>
    </ul>
  </div>
</section>

</body>
</html>
```